Kelo Wave Mint Business cards

Logo, tag line and photo on card
Agent Name
Title
Address
Phone number
Email
Website
Make logo on one side large by rotating  to portrait format.  Keep the background of the logo white.

Contact Information for Business Card
Slogan; Making Every Wave Count

```html
<!DOCTYPE html>
<html lang="en">
<head>
<meta charset="utf-8">
<title>Kelo Wave Mint Business Cards</title>
<link href="https://fonts.googleapis.com/css2?family=Montserrat:wght@300;400;600;700;800&display=swap" rel="stylesheet">
<style>
  :root{
    --bg:#e6e6e8;
    --card:#ffffff;
    --navy:#0d2a6b;
    --red:#c20a12;
    --ink:#1b1b1f;
    --faint:#e9ecf4;
    --photo-a:#cfcfcf;
    --photo-b:#6d6d6d;
  }
  *{margin:0;padding:0;box-sizing:border-box}
  html,body{width:1200px;height:1108px;overflow:hidden;background:var(--bg);font-family:'Montserrat',sans-serif}
  .card{position:absolute;background:var(--card);overflow:hidden;box-shadow:0 10px 24px rgba(0,0,0,.12)}
  .card-front{left:228px;top:67px;width:757px;height:436px}
  .card-back{left:210px;top:575px;width:779px;height:444px}

  .portrait{position:absolute;left:15px;top:28px;width:318px;height:330px;
    background:radial-gradient(ellipse at 45% 35%,var(--photo-a) 0%,#9a9a9a 45%,var(--photo-b) 80%,rgba(255,255,255,0) 100%)}
  .bands{position:absolute;left:0;top:0}

  .agent{position:absolute;left:40px;top:364px;color:#fff}
  .agent-name{font-weight:700;font-size:30px;letter-spacing:.5px;line-height:1}
  .agent-title{font-weight:300;font-size:19.5px;letter-spacing:.6px;margin-top:9px}
  .slogan{position:absolute;right:47px;top:404px;color:#fff;font-weight:700;font-size:19.5px}

  .brand-front{position:absolute;left:584px;top:40px;width:150px;color:var(--navy);
    font-weight:800;font-size:46px;line-height:52px;text-align:center;letter-spacing:-1px}

  .contacts{position:absolute;right:28px;top:230px;text-align:right;color:var(--ink);font-size:19.5px;line-height:29px;font-weight:400}
  .contact-row{display:flex;justify-content:flex-end;align-items:center;gap:10px}
  .contact-row svg{width:20px;height:20px;flex:none}
  .address{position:absolute;right:28px;top:329px;text-align:right;color:var(--ink);font-size:19.5px;line-height:29px;padding-right:0}

  .brand-back{position:absolute;left:33px;top:78px;width:340px;height:272px;display:flex;align-items:center;justify-content:center}
  .brand-back-name{transform:rotate(90deg);color:var(--navy);font-weight:800;font-size:62px;line-height:72px;text-align:center;letter-spacing:-1px;white-space:nowrap}
  .brand-faint{position:absolute;left:410px;top:40px;width:345px;color:var(--faint);font-weight:800;font-size:96px;line-height:120px;text-align:center;letter-spacing:-2px}
</style>
</head>
<body>
  <section class="card card-front">
    <div class="portrait" role="img" aria-label="Portrait photo of the managing director"></div>
    <svg class="bands" width="757" height="436" viewBox="0 0 757 436">
      <polygon points="388,394 757,394 757,436 401,436" fill="var(--red)"/>
      <polygon points="0,350 379,350 401,436 0,436" fill="var(--navy)"/>
    </svg>
    <div class="agent">
      <div class="agent-name">MARCUS ELLERY</div>
      <div class="agent-title">MANAGING DIRECTOR</div>
    </div>
    <div class="slogan">Making Every Wave Count</div>

    <div class="brand-front">Kelo<br>Wave<br>Mint</div>

    <div class="contacts">
      <div class="contact-row">044-318 702 645
        <svg viewBox="0 0 24 24"><path d="M6.6 10.8a15 15 0 0 0 6.6 6.6l2.2-2.2a1 1 0 0 1 1-.25 11.4 11.4 0 0 0 3.6.6 1 1 0 0 1 1 1V20a1 1 0 0 1-1 1A17 17 0 0 1 3 4a1 1 0 0 1 1-1h3.5a1 1 0 0 1 1 1c0 1.25.2 2.45.6 3.6a1 1 0 0 1-.25 1z" fill="var(--red)"/></svg>
      </div>
      <div class="contact-row">hello@kelowave.com
        <svg viewBox="0 0 24 24"><rect x="2" y="5" width="20" height="14" fill="var(--red)"/><path d="M2 5l10 8 10-8" fill="none" stroke="#fff" stroke-width="1.6"/></svg>
      </div>
      <div class="contact-row">www.kelowavemint.com
        <svg viewBox="0 0 24 24" fill="none" stroke="var(--red)" stroke-width="1.8"><circle cx="12" cy="12" r="9"/><ellipse cx="12" cy="12" rx="4" ry="9"/><path d="M3 12h18M4.5 7.5h15M4.5 16.5h15"/></svg>
      </div>
    </div>
    <div class="address">421, Address line goes here<br>45452, Country name</div>
  </section>

  <section class="card card-back">
    <div class="brand-back"><div class="brand-back-name">Kelo<br>Wave<br>Mint</div></div>
    <div class="brand-faint">Kelo<br>Wave<br>Mint</div>
  </section>
</body>
</html>
```